Local Flower Farm Needs Business Card Design

I need business cards designed for a flower farm based in Eudora, Kansas.
Business Info:
We are a local cut flower farm located in Eudora, Kansas, founded by Corinne Haldwick. What started as a passion for agriculture and search for more joy in daily life has blossomed into a small business dedicated to providing the community with beautiful, fresh, and sustainable flowers. We specialize in local, seasonal blooms, ensuring that every petal reflects the care and dedication we pour into our craft. Our mission is to deliver the highest quality flowers directly to our customers through local farmers markets and to florists who share our commitment to sustainability. Join us in celebrating the beauty of nature, one bloom at a time!
Contact Details:
Corinne Haldwick
Owner
Phone 913-555-0147
Facebook: Rosalind Thorpe Gardens
Instagram: @RosalindThorpeGardens
Website: RosalindThorpeGardens.example
Target Market(s)
Wholesale to Florists and Direct to Consumer via Farmers Market
Industry/Entity Type
Florist, Farm
Contact Information for Business Card
Name, Contact Info, Logo
Look and feel
Each slider illustrates characteristics of the customer's brand and the style your logo design should communicate.

```html
<!DOCTYPE html>
<html lang="en">
<head>
<meta charset="utf-8">
<title>Rosalind Thorpe Gardens – Business Card</title>
<link href="https://fonts.googleapis.com/css2?family=Tinos:wght@400;700&display=swap" rel="stylesheet">
<style>
  :root {
    --backdrop: #dfe4e6;
    --deep-teal: #0b2830;
    --paper: #ffffff;
    --ink: #111111;
    --faint: #ececec;
  }
  * { margin: 0; padding: 0; box-sizing: border-box; }
  html, body { width: 1200px; height: 960px; overflow: hidden; }
  body {
    background: var(--backdrop);
    font-family: "Tinos", "Times New Roman", serif;
    position: relative;
  }
  .card {
    position: absolute;
    left: 246px;
    width: 708px;
    height: 404px;
    overflow: hidden;
  }
  .card-front { top: 58px; background: var(--deep-teal); }
  .card-back  { top: 500px; background: var(--paper); }

  .brand-ring {
    position: absolute;
    left: 219px; top: 67px;
    width: 270px; height: 270px;
    border: 1px solid var(--paper);
    border-radius: 50%;
    display: flex; align-items: center; justify-content: center;
  }
  .brand-name {
    color: var(--paper);
    font-weight: 400;
    font-size: 25px;
    line-height: 1.35;
    letter-spacing: 3px;
    text-transform: uppercase;
    text-align: center;
  }

  .faint-brand {
    position: absolute;
    left: 260px; top: 110px;
    width: 190px;
    color: var(--faint);
    font-weight: 400;
    font-size: 34px;
    line-height: 1.2;
    text-align: center;
  }
  .identity {
    position: absolute;
    left: 28px; top: 165px;
    text-align: right;
  }
  .person-name {
    font-weight: 700;
    font-size: 33px;
    color: var(--ink);
    letter-spacing: 0.5px;
    line-height: 1.1;
  }
  .person-role {
    font-size: 17px;
    color: var(--ink);
    letter-spacing: 0.5px;
  }
  .contact-list {
    position: absolute;
    left: 392px; top: 153px;
    list-style: none;
  }
  .contact-item {
    display: flex; align-items: center;
    height: 24px;
    font-size: 17px;
    color: var(--ink);
    letter-spacing: 0.6px;
  }
  .contact-icon {
    width: 14px; height: 14px;
    margin-right: 8px;
    flex: none;
  }
</style>
</head>
<body>
  <section class="card card-front" aria-label="Card front">
    <div class="brand-ring">
      <p class="brand-name">Rosalind<br>Thorpe<br>Gardens</p>
    </div>
  </section>

  <section class="card card-back" aria-label="Card back">
    <p class="faint-brand" aria-hidden="true">Rosalind Thorpe Gardens</p>

    <div class="identity">
      <p class="person-name">Corinne Haldwick</p>
      <p class="person-role">Owner</p>
    </div>

    <ul class="contact-list">
      <li class="contact-item">
        <svg class="contact-icon" viewBox="0 0 24 24" aria-hidden="true">
          <path fill="var(--deep-teal)" d="M6.6 10.8a15.1 15.1 0 0 0 6.6 6.6l2.2-2.2c.3-.3.7-.4 1-.2 1.1.4 2.3.6 3.6.6.6 0 1 .4 1 1V20c0 .6-.4 1-1 1A17 17 0 0 1 3 4c0-.6.4-1 1-1h3.5c.6 0 1 .4 1 1 0 1.3.2 2.5.6 3.6.1.3 0 .7-.2 1z"/>
        </svg>
        913-555-0147
      </li>
      <li class="contact-item">
        <svg class="contact-icon" viewBox="0 0 24 24" aria-hidden="true">
          <circle cx="12" cy="12" r="11" fill="var(--deep-teal)"/>
        </svg>
        Rosalind Thorpe Gardens
      </li>
      <li class="contact-item">
        <svg class="contact-icon" viewBox="0 0 24 24" aria-hidden="true">
          <rect x="2" y="2" width="20" height="20" rx="5" fill="none" stroke="var(--deep-teal)" stroke-width="2.5"/>
        </svg>
        @RosalindThorpeGardens
      </li>
      <li class="contact-item">
        <svg class="contact-icon" viewBox="0 0 24 24" aria-hidden="true">
          <circle cx="12" cy="12" r="10" fill="none" stroke="var(--deep-teal)" stroke-width="2"/>
          <ellipse cx="12" cy="12" rx="4.5" ry="10" fill="none" stroke="var(--deep-teal)" stroke-width="1.6"/>
          <line x1="2" y1="12" x2="22" y2="12" stroke="var(--deep-teal)" stroke-width="1.6"/>
        </svg>
        RosalindThorpeGardens.example
      </li>
    </ul>
  </section>
</body>
</html>
```